Brell Stone Company Business Cards

Front and Back Business Card - logo and text setup - cool design. I need workable photoshop or illustrator files so I can setup each employee card with design that is created
Updates

Hi everyone, thank you for the great entries. Please no more white and blue cards - there are so many already - black and silver only now please. thanks!

Target Market(s)

Construction Industry - Facility Managers

Industry/Entity Type

Construction

Contact Information for Business Card

I really like contemporary simplistic looks - clean neat....not opposed to seeing some black backrounds

Requirements
Must have
• Logo/website address with design on front only - www.brellstone-example.com (logo attached)
• Back:
• Name/Title/Company Address/Phone/email address
Nice to have
• Cool design
Should not have
• Nothing gimmicky like Fire or Water - since we are a Fire Protection company - it has all been done

```html
<!DOCTYPE html>
<html lang="en">
<head>
<meta charset="utf-8">
<title>Brell Stone Company – Business Cards</title>
<link rel="stylesheet" href="https://fonts.googleapis.com/css2?family=Montserrat:wght@700;800&family=Alegreya:wght@400;500&display=swap">
<style>
  :root {
    --backdrop: #1b1b1b;
    --card-top: #1e1e1e;
    --card-bottom: #0c0c0c;
    --accent: #e8472f;
    --brand-blue: #2e4f9c;
    --ink: #f1f1f1;
    --ink-soft: #d9d9d9;
    --rule: #e8472f;
  }
  * { box-sizing: border-box; margin: 0; padding: 0; }
  html, body {
    width: 1200px;
    height: 800px;
    overflow: hidden;
    background: var(--backdrop);
  }
  .stage {
    position: relative;
    width: 1200px;
    height: 800px;
    display: flex;
    justify-content: center;
    align-items: center;
    gap: 50px;
  }
  .card {
    position: relative;
    width: 330px;
    height: 576px;
    background: linear-gradient(180deg, var(--card-top) 0%, var(--card-bottom) 100%);
    border-radius: 3px;
    box-shadow: 0 18px 40px rgba(0,0,0,0.55);
    display: flex;
    flex-direction: column;
    align-items: center;
    color: var(--ink);
    font-family: "Alegreya", Georgia, serif;
  }
  /* Contact side */
  .card--contact { padding-top: 98px; }
  .brand-name {
    display: flex;
    align-items: center;
    gap: 10px;
    font-family: "Montserrat", Arial, sans-serif;
    font-weight: 800;
    font-size: 38px;
    letter-spacing: -0.5px;
    color: var(--brand-blue);
  }
  .brand-mark {
    width: 14px;
    height: 14px;
    background: var(--accent);
  }
  .person-name {
    margin-top: 62px;
    font-family: "Montserrat", Arial, sans-serif;
    font-weight: 700;
    font-size: 19px;
    letter-spacing: 0.5px;
    color: var(--accent);
  }
  .person-title {
    margin-top: 6px;
    font-size: 15px;
    letter-spacing: 0.4px;
    color: var(--ink);
  }
  .icon-row {
    margin-top: 20px;
    display: flex;
    align-items: center;
    gap: 6px;
  }
  .icon-row .rule {
    width: 26px;
    height: 1px;
    background: var(--rule);
  }
  .icon-row svg { display: block; }
  .contact-list {
    margin-top: 12px;
    list-style: none;
    text-align: center;
    font-size: 15px;
    line-height: 20px;
    letter-spacing: 0.4px;
  }
  .highlight { color: var(--accent); }
  .divider {
    margin-top: 16px;
    width: 128px;
    height: 1px;
    background: var(--rule);
  }
  .address {
    margin-top: 22px;
    font-style: normal;
    text-align: center;
    font-size: 15px;
    line-height: 21px;
    letter-spacing: 0.4px;
  }
  .address .company { color: var(--accent); }
  /* Logo side */
  .card--brand { justify-content: flex-start; padding-top: 200px; }
  .card--brand .brand-name { font-size: 44px; }
  .web-address {
    margin-top: 160px;
    font-size: 15px;
    letter-spacing: 0.8px;
    color: var(--ink);
  }
</style>
</head>
<body>
<main class="stage">
  <section class="card card--contact" aria-label="Business card, contact side">
    <div class="brand-name"><span class="brand-mark"></span>Brell Stone</div>
    <h1 class="person-name">DANA WHITLOCK</h1>
    <p class="person-title">Senior Consultant</p>
    <div class="icon-row" aria-hidden="true">
      <span class="rule"></span>
      <svg width="18" height="18" viewBox="0 0 18 18">
        <circle cx="9" cy="9" r="9" fill="#e8472f"/>
        <path d="M6 4.5c.6-.3 1.2 0 1.4.5l.6 1.4c.2.4 0 .9-.3 1.1l-.6.4c.5 1.1 1.3 1.9 2.4 2.4l.4-.6c.2-.3.7-.5 1.1-.3l1.4.6c.5.2.8.8.5 1.4-.4.8-1.2 1.3-2.1 1.1C8.3 12 6 9.7 5.5 7.2c-.2-.9.2-1.9.5-2.7z" fill="#1a1a1a"/>
      </svg>
      <svg width="18" height="18" viewBox="0 0 18 18">
        <circle cx="9" cy="9" r="9" fill="#e8472f"/>
        <rect x="4.5" y="6" width="9" height="6.5" fill="none" stroke="#1a1a1a" stroke-width="1.2"/>
        <path d="M4.5 6 9 9.6 13.5 6" fill="none" stroke="#1a1a1a" stroke-width="1.2"/>
      </svg>
      <svg width="18" height="18" viewBox="0 0 18 18">
        <circle cx="9" cy="9" r="9" fill="#e8472f"/>
        <circle cx="9" cy="9" r="4.6" fill="none" stroke="#1a1a1a" stroke-width="1.1"/>
        <ellipse cx="9" cy="9" rx="2" ry="4.6" fill="none" stroke="#1a1a1a" stroke-width="1.1"/>
        <path d="M4.4 9h9.2" stroke="#1a1a1a" stroke-width="1.1"/>
      </svg>
      <span class="rule"></span>
    </div>
    <ul class="contact-list">
      <li>555.014.2290</li>
      <li>info@brellstone-example.com</li>
      <li>www.<span class="highlight">brellstone</span>-example.com</li>
    </ul>
    <span class="divider"></span>
    <address class="address">
      <span class="company">brellstone inc.</span><br>
      48 Quarry Lane Suite 2<br>
      Millbrook, NY 10000
    </address>
  </section>

  <section class="card card--brand" aria-label="Business card, logo side">
    <div class="brand-name"><span class="brand-mark"></span>Brell Stone</div>
    <p class="web-address">www.<span class="highlight">brellstone</span>-example.com</p>
  </section>
</main>
</body>
</html>
```